Want to go online this week, rush project, everything is there, just make it pretty

I need a pretty html5/css template for a already made site. Please do not rearrange anything unless you feel you can simplify the design. I have a raw site. Please play with the site by making an account with coupon code BRIGHTPEARL for free signup. Log in, log out, download as many designs as you can, then log in and log out. See everything cause it's brand new and I need it neat and pretty over the next few days if not sooner. So, after all that, the site is http://StitchLoomPatternsHub.example
Updates

Project Deadline Extended
Reason: Extending until the 30th to give more time.

Is anyone working on something to submit? If you have something please submit asap as I will be closing this Sat night or Sunday morning

Industry/Entity Type

Online

Coding

Coded - Design and coding required

```html
<!DOCTYPE html>
<html lang="en">
<head>
<meta charset="utf-8">
<title>StitchLoomPatternsHub – Machine Embroidery Designs</title>
<link href="https://fonts.googleapis.com/css2?family=Open+Sans:wght@400;600;700;800&display=swap" rel="stylesheet">
<style>
:root{
  --pink:#f57bb0;
  --pink-deep:#ee4a93;
  --green:#7cba5c;
  --blue:#93d6e6;
  --text:#555555;
  --muted:#9a9a9a;
  --line:#e6e6e6;
  --footer:#f4f4f4;
  --white:#ffffff;
}
*{box-sizing:border-box;margin:0;padding:0}
html,body{width:1200px;height:2261px;overflow:hidden}
body{font-family:"Open Sans",Arial,sans-serif;color:var(--text);background:var(--white);position:relative;border-top:3px solid var(--pink)}
a{color:inherit;text-decoration:none}
.abs{position:absolute}

/* header */
.brand{left:128px;top:24px;height:60px;display:flex;align-items:center;gap:10px;font-size:22px;font-weight:700;color:var(--green)}
.brand-dot{width:20px;height:20px;border-radius:50%;background:var(--pink)}
.top-links{right:128px;top:24px;text-align:right;font-size:17px;font-weight:600;color:var(--pink);text-transform:uppercase;line-height:1}
.top-links div{display:flex;justify-content:flex-end;align-items:center;gap:10px}
.top-links div+div{margin-top:26px}

/* nav */
.main-nav{left:128px;top:115px;width:944px;height:60px;background:var(--pink);display:flex;align-items:center}
.main-nav a{font-size:12px;color:var(--white);text-transform:uppercase;padding:0 25px;height:60px;line-height:60px}
.main-nav a.active{background:var(--green);width:95px;text-align:center;padding:0}
.main-nav .nav-search{margin-left:auto;width:51px;background:var(--pink-deep);display:flex;align-items:center;justify-content:center;padding:0}

/* hero */
.hero{left:128px;top:185px;width:944px;height:579px;background:linear-gradient(135deg,#f3f3f3 0%,#dcdcdc 40%,#c9a9a0 55%,#b7c4d0 75%,#8d7364 100%)}
.hero-arrow{top:459px;width:50px;height:50px;border-radius:50%;border:2px solid rgba(255,255,255,.8);background:rgba(0,0,0,.25);display:flex;align-items:center;justify-content:center}

/* stats */
.stats{left:128px;top:791px;width:944px;height:118px;display:flex}
.stat{flex:1;color:var(--white);text-align:center;padding-top:10px;font-size:18px;line-height:1.3}
.stat strong.big{display:block;font-size:36px;font-weight:800;line-height:1.15}
.stat.pink{background:var(--pink)}
.stat.blue{background:var(--blue)}
.stat.green{background:var(--green)}

/* sidebar */
.sidebar{left:128px;top:932px;width:217px;height:643px;background:#f7f7f7;border:1px solid #eeeeee}
.sidebar h3{height:37px;line-height:37px;background:var(--pink);color:var(--white);font-size:12px;font-weight:600;text-align:center;text-transform:uppercase}
.cat-list{list-style:none;padding:16px 0 0 18px}
.cat-list li{font-size:12px;line-height:14px;min-height:28.3px;padding-left:20px;position:relative}
.cat-list li::before{content:"»";position:absolute;left:0;top:-3px;color:var(--pink-deep);font-size:15px;font-weight:700}
.side-promo{left:128px;top:1598px;width:217px;height:231px;background:linear-gradient(180deg,#a7dcea 0%,#c5e9f2 60%,#e9f6fa 100%);padding:16px 18px;color:var(--white);font-size:19px;line-height:1.25}
.side-promo strong{font-size:34px;font-weight:700;display:block;line-height:1.1}

/* search + grid */
.search-bar{left:372px;top:935px;width:700px;height:34px;border:1px solid #dddddd;border-radius:17px;display:flex;align-items:center;padding-left:16px;font-size:12px;color:#777}
.search-btn{position:absolute;right:-1px;top:-1px;width:46px;height:34px;border-radius:0 17px 17px 0;background:var(--pink-deep);display:flex;align-items:center;justify-content:center}
.grid{left:375px;top:990px;width:695px;display:grid;grid-template-columns:repeat(3,213px);column-gap:28px;row-gap:23px}
.design-card{height:264px;border:1px solid var(--line);position:relative;background:var(--white)}
.card-art{height:137px;margin:3px}
.view-set{position:absolute;right:6px;top:75px;width:56px;height:56px;border-radius:50%;background:var(--pink-deep);color:var(--white);font-size:13px;font-weight:700;line-height:15px;text-align:center;display:flex;align-items:center;justify-content:center}
.card-title{font-size:14px;font-weight:700;color:#555;padding:10px 0 0 19px}
.card-meta{font-size:12px;color:var(--muted);padding:8px 0 0 19px;line-height:17px}
.dl-btn{position:absolute;left:0;right:0;bottom:12px;height:36px;background:var(--green);color:var(--white);font-size:16px;font-weight:700;text-align:center;line-height:36px;box-shadow:0 6px 6px -4px rgba(0,0,0,.25)}

/* pagination */
.pager{left:607px;top:1875px;display:flex;align-items:center;gap:6px}
.pager span{width:22px;height:22px;border-radius:50%;background:#dddddd;color:var(--white);font-size:11px;display:flex;align-items:center;justify-content:center}
.pager span.current{background:var(--pink-deep)}
.pager .dots{width:144px;height:0;border-radius:0;border-top:1px dotted #bbbbbb;background:none}

/* footer */
.footer{left:0;top:1972px;width:1200px;height:229px;background:var(--footer)}
.foot-col{top:2012px}
.foot-col h4{font-size:17px;font-weight:400;color:#666;text-transform:uppercase;margin-bottom:22px}
.foot-links{list-style:none;font-size:11px;line-height:19.6px;color:#777}
.contact-list{list-style:none;font-size:11px;color:#888}
.contact-list li{display:flex;gap:10px;margin-bottom:13px;line-height:14px}
.contact-list u{text-decoration:underline}
.tweet{display:flex;gap:8px;font-size:10px;margin-bottom:12px;line-height:14px;color:#888}
.tweet-date{color:var(--green)}
.tweet-dot{width:12px;height:12px;border-radius:50%;background:var(--pink-deep);flex:none;margin-top:2px}
.news-text{font-size:10px;line-height:15px;color:#888;width:210px}
.news-form{margin-top:12px;width:200px;height:36px;border:1px solid #dddddd;border-radius:4px;background:var(--white);display:flex;align-items:center;padding-left:10px;font-size:10px;font-style:italic;color:#aaa;position:relative}
.news-btn{position:absolute;right:3px;top:3px;width:36px;height:28px;background:var(--pink-deep);display:flex;align-items:center;justify-content:center}
.bottom-bar{left:0;top:2201px;width:1200px;height:60px;background:var(--pink);color:var(--white);font-size:9px;line-height:18px;padding:14px 0 0 128px}
.social{right:200px;top:2224px;display:flex;gap:14px}
.social span{width:14px;height:14px;border-radius:50%;background:var(--white)}
.bar-code{right:115px;top:2222px;font-size:10px;color:var(--white)}
</style>
</head>
<body>

<header>
  <a class="brand abs" href="#"><span class="brand-dot"></span>StitchLoomPatternsHub</a>
  <div class="top-links abs">
    <div>
      <svg width="28" height="18" viewBox="0 0 28 18"><rect x="0" y="2" width="17" height="11" fill="#7cba5c"/><path d="M17 5h6l4 4v4H17z" fill="#7cba5c"/><circle cx="6" cy="15" r="3" fill="#7cba5c"/><circle cx="22" cy="15" r="3" fill="#7cba5c"/></svg>
      Today's Free Design
    </div>
    <div>Get Notified of New Designs!</div>
  </div>
  <nav class="main-nav abs">
    <a class="active" href="#">Home</a>
    <a href="#">Register</a>
    <a href="#">Account</a>
    <a href="#">Contact</a>
    <a href="#">Search</a>
    <a href="#">Bookmark This Page</a>
    <a class="nav-search" href="#" aria-label="Search">
      <svg width="20" height="20" viewBox="0 0 20 20"><circle cx="7" cy="7" r="5" fill="none" stroke="#fff" stroke-width="2.5"/><path d="M11 11l6 6" stroke="#fff" stroke-width="3" stroke-linecap="round"/></svg>
    </a>
  </nav>
</header>

<section class="hero abs" role="img" aria-label="Close-up photo of hands guiding fabric through a white sewing machine"></section>
<a class="hero-arrow abs" style="left:146px" href="#" aria-label="Previous slide"><svg width="18" height="20" viewBox="0 0 18 20"><path d="M14 2L4 10l10 8z" fill="#fff"/></svg></a>
<a class="hero-arrow abs" style="left:1004px" href="#" aria-label="Next slide"><svg width="18" height="20" viewBox="0 0 18 20"><path d="M4 2l10 8-10 8z" fill="#fff"/></svg></a>

<section class="stats abs">
  <div class="stat pink"><strong class="big">27,906</strong>unique designs <strong>online 1,982</strong><br>Design sets/packs</div>
  <div class="stat blue"><strong class="big">REGISTER</strong>for unlimited embroidery<br>Design Downloads!</div>
  <div class="stat green"><strong class="big">GET ALL</strong>Designs on DVD<br>coming soon</div>
</section>

<aside class="sidebar abs">
  <h3>Shop by Category</h3>
  <ul class="cat-list">
    <li>Muscle Cars 2</li>
    <li>Cute Applique Monsters</li>
    <li>Applique Hot Air Balloons</li>
    <li>Swirly Cat Faces 2</li>
    <li>The Hunt</li>
    <li>Black Cats</li>
    <li>Light As A Feather</li>
    <li>Halloween With Mikayla</li>
    <li>Outer Space</li>
    <li style="min-height:42px">Dressed Up Daisy Bear Paper Dolls</li>
    <li>Halloween Cuties</li>
    <li>Tiaras</li>
    <li>Chevron Monogram</li>
    <li>Wild Animal Heads</li>
    <li>Not So Scary Bears</li>
    <li>Winged Dragons</li>
    <li>Sunflower Hanging</li>
    <li>Chevron Monogram</li>
    <li>Not So Scary Bears</li>
    <li>Pocket Happy Faces</li>
  </ul>
</aside>
<div class="side-promo abs" role="img" aria-label="Soft blue photo of an embroidery machine behind promo text"><strong>27,906</strong>lorem ipsum<br><b>online 1,982</b><br>Dolorsit<br>sets/packs</div>

<div class="search-bar abs">Search<span class="search-btn"><svg width="18" height="18" viewBox="0 0 20 20"><circle cx="7" cy="7" r="5" fill="none" stroke="#fff" stroke-width="2.5"/><path d="M11 11l6 6" stroke="#fff" stroke-width="3" stroke-linecap="round"/></svg></span></div>

<main class="grid abs">
  <article class="design-card"><div class="card-art" role="img" aria-label="Embroidered purple muscle car" style="background:linear-gradient(135deg,#f4f4f4,#d9d3e6)"></div><span class="view-set">VIEW<br>SET</span><h2 class="card-title">MUSCLE CARS 2</h2><p class="card-meta">10 Designs<br>All Fit the 4x4 Hoop</p><a class="dl-btn" href="#">DOWNLOAD NOW</a></article>
  <article class="design-card"><div class="card-art" role="img" aria-label="Green applique monster embroidery" style="background:linear-gradient(135deg,#eef0ee,#b9dc9a)"></div><span class="view-set">VIEW<br>SET</span><h2 class="card-title">MUSCLE CARS 2</h2><p class="card-meta">10 Designs<br>All Fit the 4x4 Hoop</p><a class="dl-btn" href="#">DOWNLOAD NOW</a></article>
  <article class="design-card"><div class="card-art" role="img" aria-label="Red and navy hot air balloon embroidery" style="background:linear-gradient(135deg,#ffffff,#e6dde4)"></div><span class="view-set">VIEW<br>SET</span><h2 class="card-title">MUSCLE CARS 2</h2><p class="card-meta">10 Designs<br>All Fit the 4x4 Hoop</p><a class="dl-btn" href="#">DOWNLOAD NOW</a></article>
  <article class="design-card"><div class="card-art" role="img" aria-label="Swirly cat face embroidery" style="background:linear-gradient(135deg,#f7f3ee,#ead6c2)"></div><span class="view-set">VIEW<br>SET</span><h2 class="card-title">MUSCLE CARS 2</h2><p class="card-meta">10 Designs<br>All Fit the 4x4 Hoop</p><a class="dl-btn" href="#">DOWNLOAD NOW</a></article>
  <article class="design-card"><div class="card-art" role="img" aria-label="Antler outline embroidery" style="background:linear-gradient(135deg,#ffffff,#ece8e4)"></div><span class="view-set">VIEW<br>SET</span><h2 class="card-title">MUSCLE CARS 2</h2><p class="card-meta">10 Designs<br>All Fit the 4x4 Hoop</p><a class="dl-btn" href="#">DOWNLOAD NOW</a></article>
  <article class="design-card"><div class="card-art" role="img" aria-label="Black cat embroidery on light fabric" style="background:linear-gradient(135deg,#e8ecef,#9fa4a8)"></div><span class="view-set">VIEW<br>SET</span><h2 class="card-title">MUSCLE CARS 2</h2><p class="card-meta">10 Designs<br>All Fit the 4x4 Hoop</p><a class="dl-btn" href="#">DOWNLOAD NOW</a></article>
  <article class="design-card"><div class="card-art" role="img" aria-label="Blue and purple feather embroidery" style="background:linear-gradient(135deg,#f2f2f4,#c9c6e0)"></div><span class="view-set">VIEW<br>SET</span><h2 class="card-title">MUSCLE CARS 2</h2><p class="card-meta">10 Designs<br>All Fit the 4x4 Hoop</p><a class="dl-btn" href="#">DOWNLOAD NOW</a></article>
  <article class="design-card"><div class="card-art" role="img" aria-label="Halloween character with pumpkins embroidery" style="background:linear-gradient(135deg,#dde3e6,#c8a47c)"></div><span class="view-set">VIEW<br>SET</span><h2 class="card-title">MUSCLE CARS 2</h2><p class="card-meta">10 Designs<br>All Fit the 4x4 Hoop</p><a class="dl-btn" href="#">DOWNLOAD NOW</a></article>
  <article class="design-card"><div class="card-art" role="img" aria-label="Gold tiara embroidery" style="background:linear-gradient(135deg,#ffffff,#f1e3c9)"></div><span class="view-set">VIEW<br>SET</span><h2 class="card-title">MUSCLE CARS 2</h2><p class="card-meta">10 Designs<br>All Fit the 4x4 Hoop</p><a class="dl-btn" href="#">DOWNLOAD NOW</a></article>
</main>

<nav class="pager abs" aria-label="Pages">
  <span class="current">1</span><span>2</span><span>3</span><span class="dots"></span><span>24</span>
</nav>

<footer>
  <div class="footer abs"></div>
  <div class="foot-col abs" style="left:128px">
    <h4>Links</h4>
    <ul class="foot-links"><li>Home</li><li>Register</li><li>Account</li><li>Contact</li><li>Search</li><li>Bookmark This Page</li></ul>
  </div>
  <div class="foot-col abs" style="left:347px">
    <h4>Contact</h4>
    <ul class="contact-list">
      <li><svg width="12" height="12" viewBox="0 0 12 12"><path d="M2 1h3l1 3-2 1a7 7 0 003 3l1-2 3 1v3c-6 1-10-3-9-9z" fill="#999"/></svg>03 5550 0182 (Phone)</li>
      <li><svg width="12" height="12" viewBox="0 0 12 12"><rect x="3" y="1" width="6" height="3" fill="#999"/><rect x="1" y="4" width="10" height="5" fill="#999"/><rect x="3" y="8" width="6" height="3" fill="#bbb"/></svg>03 5550 0183 (Fax)</li>
      <li><svg width="12" height="12" viewBox="0 0 12 12"><rect x="1" y="3" width="10" height="7" fill="#999"/><path d="M1 3l5 4 5-4" stroke="#fff" fill="none"/></svg><u>hello@stitchloom.example</u></li>
      <li><svg width="12" height="12" viewBox="0 0 12 12"><path d="M6 11S2 7 2 4.5a4 4 0 018 0C10 7 6 11 6 11z" fill="#999"/><circle cx="6" cy="4.5" r="1.5" fill="#fff"/></svg><span>PO Box: 4420, Ferndale<br>lorem si7261</span></li>
    </ul>
  </div>
  <div class="foot-col abs" style="left:604px">
    <h4>Tweets</h4>
    <div class="tweet"><span class="tweet-dot"></span><div><span class="tweet-date">Tue, April 19, 2011</span><br>Loom Club is excited to share its<br>new pattern release this week......</div></div>
    <div class="tweet"><span class="tweet-dot"></span><div><span class="tweet-date">Tue, April 19, 2011</span><br>Loom Club is excited to share its<br>new pattern release this week......</div></div>
  </div>
  <div class="foot-col abs" style="left:861px">
    <h4>Newsletter</h4>
    <p class="news-text">Enter your email address below to subscribe. You will receive our newsletter once a week.</p>
    <div class="news-form">enter your email address<span class="news-btn"><svg width="10" height="12" viewBox="0 0 10 12"><path d="M2 1l5 5-5 5" stroke="#fff" stroke-width="2" fill="none"/></svg></span></div>
  </div>
  <div class="bottom-bar abs">Website and Embroidery Designs Copyright (C) Marlow Thread Works Inc.<br>Permission granted to use machine embroidery designs for your own commercial and personal embroidery.</div>
  <div class="social abs"><span></span><span></span><span></span><span></span></div>
  <div class="bar-code abs">C4</div>
</footer>

</body>
</html>
```